Vantro cards

I am in the auto motive, transportation business I would like a business card that is Something cool, modern edgy, having to do with car culture. I offer towing service for high and exotic cars. I also provide towing for collisions and car accidents. I offer open and enclosed transport nationwide.

Target Market(s)

Car culture people high end auto collectors

Industry/Entity Type

Towing car carrier

Contact Information for Business Card

My company colors black yellow and silver

Font styles to use
Serif

```html
<!DOCTYPE html>
<html lang="en">
<head>
<meta charset="utf-8">
<title>Vantro Business Cards</title>
<link rel="stylesheet" href="https://fonts.googleapis.com/css2?family=Roboto+Slab:wght@400;500&family=Lato:wght@400&display=swap">
<style>
  :root {
    --backdrop: #3a3a3c;
    --card-black: #1e1e1f;
    --card-edge: #f2d64b;
    --accent-yellow: #f4d94a;
    --text-silver: #e6e6e6;
    --shadow: rgba(0, 0, 0, 0.45);
  }
  * { box-sizing: border-box; margin: 0; padding: 0; }
  html, body {
    width: 1200px;
    height: 800px;
    overflow: hidden;
    background: var(--backdrop);
  }
  .sheet {
    width: 1200px;
    height: 800px;
    display: flex;
    align-items: center;
    justify-content: center;
    gap: 44px;
  }
  .card {
    position: relative;
    width: 520px;
    height: 297px;
    background: var(--card-black);
    border-radius: 16px;
    border-bottom: 4px solid var(--card-edge);
    box-shadow: 0 18px 36px var(--shadow);
    overflow: hidden;
  }
  .card-front {
    display: flex;
    align-items: center;
    padding: 0 40px 0 52px;
  }
  .identity {
    text-align: right;
    padding-right: 22px;
  }
  .identity-name {
    font-family: "Roboto Slab", serif;
    font-weight: 400;
    font-size: 25px;
    letter-spacing: 1px;
    color: var(--accent-yellow);
    text-transform: uppercase;
  }
  .identity-title {
    font-family: "Roboto Slab", serif;
    font-size: 14px;
    letter-spacing: 0.5px;
    color: var(--text-silver);
    margin-top: 2px;
  }
  .divider {
    width: 2px;
    height: 62px;
    background: var(--accent-yellow);
    flex-shrink: 0;
  }
  .contact-list {
    list-style: none;
    padding-left: 22px;
  }
  .contact-item {
    display: flex;
    align-items: center;
    gap: 10px;
    font-family: "Lato", sans-serif;
    font-size: 13px;
    color: var(--text-silver);
    line-height: 1.7;
  }
  .contact-item.phone { font-size: 15px; }
  .contact-icon {
    width: 12px;
    height: 12px;
    flex-shrink: 0;
  }
  .card-back {
    display: flex;
    align-items: center;
    justify-content: center;
  }
  .brand-name {
    font-family: "Roboto Slab", serif;
    font-weight: 500;
    font-size: 52px;
    letter-spacing: 4px;
    color: var(--accent-yellow);
    text-transform: uppercase;
  }
</style>
</head>
<body>
<main class="sheet">
  <section class="card card-front" aria-label="Business card front">
    <div class="identity">
      <h1 class="identity-name">Daniel Corvell</h1>
      <p class="identity-title">Managing Director</p>
    </div>
    <div class="divider"></div>
    <ul class="contact-list">
      <li class="contact-item phone">
        <svg class="contact-icon" viewBox="0 0 24 24" aria-hidden="true"><path fill="#f4d94a" d="M6.6 10.8a15.1 15.1 0 0 0 6.6 6.6l2.2-2.2a1 1 0 0 1 1-.25 11.4 11.4 0 0 0 3.6.57 1 1 0 0 1 1 1V20a1 1 0 0 1-1 1A17 17 0 0 1 3 4a1 1 0 0 1 1-1h3.5a1 1 0 0 1 1 1c0 1.25.2 2.45.57 3.57a1 1 0 0 1-.25 1z"/></svg>
        555-218-4073
      </li>
      <li class="contact-item">
        <svg class="contact-icon" viewBox="0 0 24 24" aria-hidden="true"><rect x="2" y="5" width="20" height="14" rx="1" fill="#f4d94a"/><path d="M2.5 6l9.5 7 9.5-7" fill="none" stroke="#1e1e1f" stroke-width="1.6"/></svg>
        corvell@vantrohaul.com
      </li>
      <li class="contact-item">
        <svg class="contact-icon" viewBox="0 0 24 24" aria-hidden="true"><circle cx="12" cy="12" r="10" fill="#f4d94a"/><path d="M2 12h20M12 2c3 3 3 17 0 20M12 2c-3 3-3 17 0 20" fill="none" stroke="#1e1e1f" stroke-width="1.4"/></svg>
        www.vantrohaul.com
      </li>
    </ul>
  </section>

  <section class="card card-back" aria-label="Business card back">
    <p class="brand-name">Vantro</p>
  </section>
</main>
</body>
</html>
```